Corinnehabbard.com

1. Conceptualization and designing of the site Homepage. The Homepage design will be completely customized and based on your design instructions (i.e. preferred colors, links to reference sites that you want us to take reference from if any etc) and the recently completed logo design.
2. Upon homepage design approval, based on it we will be creating the layout for the other 4 site inner pages (i.e. About page, Contact page, Services page, and Insights (publications, media).
3. Once all the inner page designs are approved, we will get the designs built (will make sure that the site is completely Responsive - works on all devices) within your provided WIX account.
4. We will add the static text and images provided by you to the Home page, About page, Contact page, and the Services page. For the 2 Insights sub-pages, we will add 1-2 sample Publications and Media entries.
once you confirm the total number of required entries for the 2 sub-pages, I will accordingly quote you on the same
5. Integration of a Contact form on the Contact page that will email the filled in details to your mail id.

```html
<!DOCTYPE html>
<html lang="en">
<head>
<meta charset="utf-8">
<title>Corinne Habbard Consulting</title>
<link href="https://fonts.googleapis.com/css2?family=League+Spartan:wght@500;600;700&family=Arimo:wght@400;700&display=swap" rel="stylesheet">
<style>
:root{
  --blue:#0a96dc;
  --green:#16902f;
  --orange:#f39000;
  --ink:#1e1e1e;
  --muted:#6b6b6b;
  --pale:#eaf6fd;
  --dark:#2b2b2b;
  --white:#ffffff;
}
*{box-sizing:border-box;margin:0;padding:0}
html,body{width:1200px;height:3875px;overflow:hidden}
body{position:relative;background:var(--white);font-family:"Arimo",Arial,sans-serif;color:var(--ink)}
.abs{position:absolute}
.heading{font-family:"League Spartan",Arial,sans-serif;font-weight:700;letter-spacing:1px}
.btn{position:absolute;display:flex;align-items:center;justify-content:center;background:var(--green);color:var(--white);font:700 13px "Arimo",Arial,sans-serif;border-radius:18px}
.ph{position:absolute}

/* header */
.site-header{position:absolute;left:0;top:0;width:1200px;height:81px;background:var(--white);z-index:3}
.brand{position:absolute;left:143px;top:18px;text-align:center;font-family:"League Spartan",Arial,sans-serif;font-weight:700;color:var(--blue);font-size:18px;line-height:20px;letter-spacing:1px}
.brand .dot{display:block;width:34px;height:34px;border:2px solid var(--blue);border-radius:50%;margin:-10px auto 4px}
.brand small{display:block;font-size:11px;letter-spacing:3px;line-height:12px}
.nav{position:absolute;top:30px;left:512px;display:flex;gap:30px;font-size:13px;color:#333}
.nav .active{color:var(--orange)}
.quote{left:922px;top:21px;width:133px;height:34px}

/* hero */
.hero{left:0;top:81px;width:1200px;height:641px;background:linear-gradient(100deg,#f2f4f6 0%,#dfe3e6 40%,#9aa6b3 70%,#4c6a96 100%)}
.hero-title{left:143px;top:326px;font-size:56px;line-height:50px;color:#222;z-index:2}
.hero-btn{left:143px;top:439px;width:133px;height:34px;z-index:2}
.arrow{position:absolute;top:610px;width:36px;height:36px;border-radius:50%;background:var(--white);display:flex;align-items:center;justify-content:center;z-index:2}
.badge{left:570px;top:692px;width:60px;height:60px;border-radius:50%;background:var(--white);border:3px solid #e6e6e6}

/* services */
.section-title{position:absolute;font-size:42px;color:var(--blue)}
.rule{position:absolute;height:3px;width:90px;background:var(--green)}
.card{position:absolute;top:907px;width:285px;height:305px;background:var(--white);box-shadow:0 2px 14px rgba(0,0,0,.08);padding:28px 28px}
.card h3{font-family:"League Spartan",Arial,sans-serif;font-weight:700;font-size:17px;margin:18px 0 18px}
.card p{font-size:12px;line-height:20px;color:var(--muted);text-align:justify}
.card.featured{background:var(--blue);color:var(--white)}
.card.featured p{color:var(--white)}

/* about */
.about{left:0;top:1332px;width:1200px;height:600px;background:var(--pale);overflow:hidden}
.about-ring{left:-120px;top:165px;width:420px;height:420px;border-radius:50%;border:4px solid #d9e3e8}
.about-photo{left:115px;top:70px;width:480px;height:480px;border-radius:50%;background:radial-gradient(circle,#e9e4dc 0 30%,#b08e74 45%,#6b8a6a 62%,#1a9a3a 70%,transparent 71%)}
.about-text{left:626px;top:1508px;width:430px;font-size:12.5px;line-height:20px;color:#555;text-align:justify}

/* stats */
.stats{left:0;top:1932px;width:1200px;height:264px;background:var(--blue)}
.stat{position:absolute;top:68px;width:286px;height:128px;border:1px solid rgba(255,255,255,.25);background:rgba(255,255,255,.04);text-align:center;color:var(--white)}
.stat::before{content:"";position:absolute;top:-2px;left:103px;width:80px;height:4px;background:var(--white)}
.stat b{display:block;font-family:"League Spartan",Arial,sans-serif;font-size:48px;margin-top:28px;line-height:46px}
.stat span{font-size:13px}

/* insights */
.post-img{position:absolute;width:217px;height:162px}
.post-title{position:absolute;font-size:16px;color:#222;width:217px}
.post-more{position:absolute;font-size:11px;font-weight:700;color:var(--green)}
.post-line{position:absolute;width:217px;height:2px;background:var(--orange)}
.tag{position:absolute;background:var(--orange);color:var(--white);font-size:11px;font-weight:700;padding:3px 6px;border-radius:3px}

/* contact */
.contact{left:0;top:2955px;width:1200px;height:534px;background:var(--orange)}
.contact-circle{left:610px;top:2910px;width:620px;height:580px;border-radius:50% 50% 0 0/50% 50% 0 0;background:var(--white)}
.contact-photo{left:700px;top:2905px;width:460px;height:584px;background:linear-gradient(180deg,#d8c1a8 0%,#f4f4f4 30%,#ffffff 60%,#9aa0a6 100%);border-radius:220px 220px 0 0}
.field{position:absolute;width:203px;border-bottom:1px solid rgba(255,255,255,.7);color:var(--white)}
.field label{display:block;font-size:10px;margin-bottom:16px}
.field div{font-size:11px;color:rgba(255,255,255,.7);padding-bottom:8px}

/* footer */
.footer{left:0;top:3489px;width:1200px;height:386px;background:var(--dark);color:var(--white)}
.f-brand{position:absolute;left:140px;top:90px;width:240px;text-align:center;font-family:"League Spartan",Arial,sans-serif;font-weight:600;font-size:22px;letter-spacing:1px;line-height:24px}
.f-brand .dot{display:block;width:86px;height:86px;border:3px solid var(--white);border-radius:50%;margin:0 auto 16px}
.f-col{position:absolute;top:104px;font-size:12px;line-height:24px}
.f-col h4{font-family:"Arimo",Arial,sans-serif;font-size:16px;margin-bottom:18px}
.f-copy{left:143px;top:319px;width:913px;display:flex;align-items:center;gap:10px;font-size:12px}
.f-copy i{flex:1;height:1px;background:rgba(255,255,255,.5)}
</style>
</head>
<body>

<header class="site-header">
  <div class="brand"><span class="dot"></span>CORINNE HABBARD<small>CONSULTING</small></div>
  <nav class="nav"><span class="active">Home</span><span>About us</span><span>Insights</span><span>Services</span><span>Contact us</span></nav>
  <div class="btn quote">Get A Quote</div>
</header>

<section>
  <div class="ph hero abs" role="img" aria-label="Photo of two business colleagues reviewing a tablet in a bright office"></div>
  <h1 class="abs heading hero-title">CORINNE<br>HABBARD</h1>
  <div class="btn hero-btn">Get Started</div>
  <div class="arrow" style="left:143px"><svg width="12" height="12" viewBox="0 0 12 12"><path d="M8 1 3 6l5 5" fill="none" stroke="#222" stroke-width="1.8"/></svg></div>
  <div class="arrow" style="left:190px"><svg width="12" height="12" viewBox="0 0 12 12"><path d="M4 1l5 5-5 5" fill="none" stroke="#222" stroke-width="1.8"/></svg></div>
  <div class="abs badge"></div>
</section>

<section>
  <h2 class="section-title heading" style="left:143px;top:818px">OUR SERVICES</h2>
  <div class="rule" style="left:143px;top:873px"></div>

  <article class="card" style="left:143px">
    <svg width="72" height="72" viewBox="0 0 72 72" fill="none" stroke="#f39000" stroke-width="2"><rect x="4" y="6" width="18" height="12" rx="2"/><rect x="30" y="4" width="20" height="14" rx="2"/><circle cx="16" cy="28" r="6"/><circle cx="56" cy="28" r="6"/><path d="M6 66V44q0-8 10-8t10 8v22M46 66V44q0-8 10-8t10 8v22M26 50h20"/></svg>
    <h3>Lorem ipsum dolor sit</h3>
    <p>Lorem ipsum dolor sit amet, consecte tur adipiscing elit, sed do eiusmod tem por incididunt ut labore et dolore magn a aliqua. Ut enim ad minim veniam, qu is nostrud exercitation ullamco laboris nisi ut aliquip commodo equat.</p>
  </article>
  <article class="card featured" style="left:457px">
    <svg width="72" height="72" viewBox="0 0 72 72" fill="none" stroke="#fff" stroke-width="2"><rect x="4" y="6" width="22" height="16" rx="2"/><rect x="30" y="6" width="34" height="20" rx="2"/><path d="M36 12h22M36 18h16"/><circle cx="18" cy="38" r="7"/><circle cx="46" cy="38" r="7"/><path d="M4 66q0-16 14-16t14 16zM32 66q0-16 14-16t14 16z"/></svg>
    <h3>Lorem ipsum dolor sit</h3>
    <p>Lorem ipsum dolor sit amet, consecte tur adipiscing elit, sed do eiusmod tem por incididunt ut labore et dolore magn a aliqua. Ut enim ad minim veniam, qu is nostrud exercitation ullamco laboris nisi ut aliquip commodo equat.</p>
  </article>
  <article class="card" style="left:772px">
    <svg width="72" height="72" viewBox="0 0 72 72" fill="none" stroke="#f39000" stroke-width="2"><circle cx="36" cy="10" r="5"/><circle cx="18" cy="20" r="5"/><circle cx="54" cy="20" r="5"/><rect x="6" y="34" width="60" height="12" rx="2"/><path d="M12 46v16M60 46v16M26 46l-4 16M46 46l4 16M30 22h12"/></svg>
    <h3>Lorem ipsum dolor sit</h3>
    <p>Lorem ipsum dolor sit amet, consecte tur adipiscing elit, sed do eiusmod tem por incididunt ut labore et dolore magn a aliqua. Ut enim ad minim veniam, qu is nostrud exercitation ullamco laboris nisi ut aliquip commodo equat.</p>
  </article>
</section>

<section class="abs about">
  <div class="abs about-ring"></div>
  <div class="ph about-photo" role="img" aria-label="Overhead photo of a team gathered around a round table joining hands"></div>
</section>
<h2 class="section-title heading" style="left:626px;top:1423px">ABOUT US</h2>
<div class="rule" style="left:626px;top:1478px"></div>
<p class="abs about-text">Lorem ipsum dolor sit amet, consectetur adipiscing elit, sed do eiusmod tempor incididunt ut labore et dolore magna aliqua. Ut enim ad minim veniam, quis nostrud exercitation ullamco laboris nisi ut aliquip ex ea commodo consequat. Duis aute irure dolor in reprehenderit in voluptate velit esse cillum dolore eu fugiat nulla pariatur. Excepteur sint occaecat cupidatat non proident, sunt in culpa qui officia deserunt mollit anim id est laborum. Lorem ipsum dolor sit amet, consectetur adipiscing elit, sed do eiusmod tempor incididunt ut labore et dolore magna aliqua. Ut enim ad minim veniam, quis nostrud exercitation ullamco laboris nisi ut aliquip ex ea commodo consequat. Duis aute irure dolor in reprehenderit in voluptate velit esse cillum dolore eu fugiat nulla pariatur. Excepteur sint occaecat cupidatat non proident, sunt in culpa qui officia deserunt mollit anim id est laborum.</p>
<div class="btn" style="left:626px;top:1782px;width:134px;height:34px">Learn More &#10140;</div>

<section class="abs stats">
  <div class="stat" style="left:143px"><b>570+</b><span>Satisfied Clients</span></div>
  <div class="stat" style="left:457px"><b>256+</b><span>Technology Candidates Placed</span></div>
  <div class="stat" style="left:770px"><b>10+</b><span>Years of Experience</span></div>
</section>

<section>
  <h2 class="section-title heading" style="left:0;width:1200px;text-align:center;top:2282px">OUR INSIGHTS</h2>
  <div class="rule" style="left:555px;top:2337px"></div>

  <div class="ph" style="left:143px;top:2375px;width:442px;height:457px;background:linear-gradient(160deg,#6b4a3a 0%,#4a2c22 50%,#2e2320 100%)" role="img" aria-label="Photo of a speaker standing beside a flag at a publication event"></div>
  <span class="tag" style="left:180px;top:2700px">PUBLICATIONS</span>
  <p class="abs" style="left:180px;top:2728px;width:372px;color:#fff;font-weight:700;font-size:16px;line-height:24px">Lorem ipsum dolor sit amet, consectetur adipisc ing elit, sed do eiusmod tempor incididunt ut labore</p>

  <div class="ph post-img" style="left:600px;top:2375px;background:linear-gradient(160deg,#6f7d86,#3d4a54)" role="img" aria-label="Photo of business people in a meeting"></div>
  <div class="post-title" style="left:600px;top:2546px">Lorem ipsum dolor sit</div>
  <div class="post-more" style="left:600px;top:2576px">Read more &#10140;</div>
  <div class="post-line" style="left:600px;top:2596px"></div>

  <div class="ph post-img" style="left:839px;top:2375px;background:linear-gradient(160deg,#8a9096,#4b5157)" role="img" aria-label="Photo of a team working at an office table"></div>
  <div class="post-title" style="left:839px;top:2546px">Lorem ipsum dolor sit</div>
  <div class="post-more" style="left:839px;top:2576px">Read more &#10140;</div>
  <div class="post-line" style="left:839px;top:2596px"></div>

  <div class="ph post-img" style="left:600px;top:2607px;background:linear-gradient(160deg,#c7c3bb,#8e7b67)" role="img" aria-label="Photo of a presenter at a whiteboard"></div>
  <div class="post-title" style="left:600px;top:2779px">Lorem ipsum dolor sit</div>
  <div class="post-more" style="left:600px;top:2809px">Read more &#10140;</div>
  <div class="post-line" style="left:600px;top:2829px"></div>

  <div class="ph post-img" style="left:839px;top:2607px;background:linear-gradient(160deg,#5d6a70,#9ea6aa)" role="img" aria-label="Photo of colleagues discussing documents"></div>
  <div class="post-title" style="left:839px;top:2779px">Lorem ipsum dolor sit</div>
  <div class="post-more" style="left:839px;top:2809px">Read more &#10140;</div>
  <div class="post-line" style="left:839px;top:2829px"></div>
</section>

<section>
  <div class="abs contact"></div>
  <div class="abs contact-circle"></div>
  <div class="ph contact-photo" role="img" aria-label="Photo of a smiling businessman holding a laptop"></div>
  <h2 class="section-title heading" style="left:143px;top:3028px;color:#fff">GET IN TOUCH</h2>
  <div class="rule" style="left:143px;top:3085px;background:#fff;width:70px"></div>

  <div class="field" style="left:145px;top:3120px"><label>First name*</label><div>JOHN</div></div>
  <div class="field" style="left:377px;top:3120px"><label>Last name*</label><div>DOE</div></div>
  <div class="field" style="left:145px;top:3208px"><label>Email*</label><div>INFO@COMPANYNAME.COM</div></div>
  <div class="field" style="left:377px;top:3208px"><label>Phone*</label><div>+1 888 888 8888</div></div>
  <div class="field" style="left:145px;top:3304px;width:435px"><label>Message*</label><div>TEXT HERE</div></div>
  <div class="btn" style="left:144px;top:3372px;width:133px;height:34px">Submit</div>
</section>

<footer class="abs footer">
  <div class="f-brand"><span class="dot"></span>CORINNE HABBARD<br><span style="font-size:17px;letter-spacing:4px">CONSULTING</span></div>
  <div class="f-col" style="left:483px"><h4>Navigation</h4>Home<br>About<br>Services<br>Insights<br>Contact</div>
  <div class="f-col" style="left:666px"><h4>Quick Links</h4>Privacy policy<br>Terms and condition<br>Support<br>Faq<br>Leagl</div>
  <div class="f-col" style="left:863px"><h4>Contact Info</h4>
    <div style="display:flex;gap:18px"><svg width="10" height="24" viewBox="0 0 10 24"><path d="M5 6a4 4 0 0 1 4 4c0 3-4 7-4 7s-4-4-4-7a4 4 0 0 1 4-4z" fill="#f39000"/></svg><span>123, Lorem ipsum dolor sit<br>amet, consec</span></div>
    <div style="display:flex;gap:18px"><svg width="10" height="24" viewBox="0 0 10 24"><path d="M1 8c0 5 4 9 8 9l1-2-3-2-1 1c-1-1-3-3-3-4l1-1-2-3z" fill="#f39000"/></svg><span>+1 888 888 8888</span></div>
    <div style="display:flex;gap:18px"><svg width="12" height="24" viewBox="0 0 12 24"><rect x="0" y="8" width="12" height="9" fill="#f39000"/><path d="M0 8l6 5 6-5" fill="none" stroke="#2b2b2b"/></svg><span>info@company name</span></div>
  </div>
  <div class="abs f-copy"><i></i><span>&copy; Copyrights 2024 Company name | All Rights Reserved</span><i></i></div>
</footer>

</body>
</html>
```